Business Card Design Project

We need a new fresh business card for our business. There are multiple services we offer and we need a fresh corporate card that represents us better. We start from cleaning carpet and tiles, to upholstery and curtains, to completely clean all contents and building materials after a fire, or completely dry out a home or business after a major or minor flood event. We are open to all concepts as we want to create a new look, maybe even logo, signage, vehicle signage, uniforms.
We are open to new colours etc.

Go to www.brolvaquincare.com.au for current logo and all other past ideas

Target Market(s)

Everyone is our possible client but we are targeting more coorporate

Industry/Entity Type

Building

```html
<!DOCTYPE html>
<html lang="en">
<head>
<meta charset="utf-8">
<title>Brolvaquin Care Services – Business Card</title>
<link rel="stylesheet" href="https://fonts.googleapis.com/css2?family=Jura:wght@500;600;700&display=swap">
<style>
  :root {
    --page: #e4e6ee;
    --card: #ffffff;
    --card-shade: #eceef1;
    --brand-blue: #1a5aa0;
    --brand-pink: #e3197f;
    --ink: #2b2b2b;
    --ink-light: #ffffff;
    --mark-ring: #b9bec6;
  }
  * { box-sizing: border-box; margin: 0; padding: 0; }
  html, body {
    width: 1200px; height: 840px; overflow: hidden;
    background: var(--page);
    font-family: "Jura", sans-serif;
  }
  .card {
    position: absolute; left: 75px; top: 120px;
    width: 1050px; height: 600px;
    background: linear-gradient(160deg, var(--card) 0%, var(--card-shade) 100%);
    box-shadow: 0 18px 40px rgba(40, 50, 80, .18);
    overflow: hidden;
  }
  .card-waves { position: absolute; inset: 0; width: 100%; height: 100%; }
  .brand {
    position: absolute; left: 48px; top: 62px;
    display: flex; align-items: center; gap: 18px;
  }
  .brand-name {
    color: var(--brand-blue);
    font-weight: 700; font-size: 36px; line-height: 1;
    letter-spacing: .5px;
  }
  .brand-dot {
    width: 90px; height: 90px; border-radius: 50%;
    border: 6px solid var(--mark-ring);
    background: var(--card);
  }
  .holder {
    position: absolute; right: 150px; top: 165px;
    text-align: right;
  }
  .holder-name {
    color: var(--ink); font-weight: 600; font-size: 34px;
    letter-spacing: 2px; text-transform: uppercase; line-height: 1.1;
  }
  .holder-role {
    color: var(--brand-blue); font-weight: 600; font-size: 22px;
    margin-top: 4px;
  }
  .address {
    position: absolute; right: 40px; top: 330px;
    color: var(--ink-light); font-weight: 600; font-size: 21px;
    text-align: right; line-height: 1.4; letter-spacing: .5px;
  }
  .contacts {
    position: absolute; left: 36px; top: 412px;
    list-style: none;
    color: var(--ink-light); font-weight: 600; font-size: 21px;
    letter-spacing: .5px;
  }
  .contacts li {
    display: flex; align-items: center; gap: 14px;
    height: 34px;
  }
  .contacts svg { width: 22px; height: 22px; flex: none; }
</style>
</head>
<body>
  <section class="card" aria-label="Business card">
    <svg class="card-waves" viewBox="0 0 1050 600" preserveAspectRatio="none" aria-hidden="true">
      <path fill="var(--brand-pink)" d="M0,362 C140,300 300,262 470,258 C300,276 150,322 0,392 Z"/>
      <path fill="var(--brand-pink)" d="M760,290 C900,270 1000,200 1050,140 L1050,185 C990,245 890,285 760,290 Z"/>
      <path fill="var(--brand-blue)" d="M0,402 C170,302 380,272 580,285 C760,297 930,290 1050,220 L1050,600 L0,600 Z"/>
      <path fill="var(--brand-blue)" d="M360,262 C520,248 640,262 720,280 C600,266 480,258 360,262 Z"/>
    </svg>

    <div class="brand">
      <span class="brand-name">Brolvaquin Care Services</span>
      <span class="brand-dot"></span>
    </div>

    <div class="holder">
      <p class="holder-name">Marcus Elden</p>
      <p class="holder-role">Managing Director</p>
    </div>

    <p class="address">41 Harwick Lane Level 3<br>Tarrowby</p>

    <ul class="contacts">
      <li>
        <svg viewBox="0 0 24 24" fill="var(--ink-light)"><path d="M6.6 10.8a15 15 0 0 0 6.6 6.6l2.2-2.2c.3-.3.7-.4 1-.2 1.1.4 2.3.6 3.6.6.6 0 1 .4 1 1V20c0 .6-.4 1-1 1A17 17 0 0 1 3 4c0-.6.4-1 1-1h3.5c.6 0 1 .4 1 1 0 1.3.2 2.5.6 3.6.1.3 0 .7-.2 1z"/></svg>
        013 482 5071
      </li>
      <li>
        <svg viewBox="0 0 24 24" fill="none" stroke="var(--ink-light)" stroke-width="2"><rect x="7" y="2" width="10" height="20" rx="2"/><line x1="11" y1="18" x2="13" y2="18"/></svg>
        013 482 5072
      </li>
      <li>
        <svg viewBox="0 0 24 24" fill="var(--ink-light)"><path d="M6 2h9l4 4v16H6z"/><rect x="9" y="11" width="7" height="2" fill="var(--brand-blue)"/><rect x="9" y="15" width="7" height="2" fill="var(--brand-blue)"/></svg>
        013 482 5073
      </li>
      <li>
        <svg viewBox="0 0 24 24" fill="none" stroke="var(--ink-light)" stroke-width="2"><rect x="3" y="5" width="18" height="14"/><path d="M3 5l9 8 9-8"/></svg>
        marcus@brolvaquincare.com.au
      </li>
      <li>
        <svg viewBox="0 0 24 24" fill="none" stroke="var(--ink-light)" stroke-width="2"><circle cx="12" cy="12" r="9"/><path d="M3 12h18M12 3c3 3 3 15 0 18M12 3c-3 3-3 15 0 18"/></svg>
        www.brolvaquincare.com.au
      </li>
    </ul>
  </section>
</body>
</html>
```